New Website

New website is to be the same as Amber Lantern.

Website needs to be fully functional, with only text and logo to be added by client at a later date.

Logo has been added for reference.

```html
<!DOCTYPE html>
<html lang="en">
<head>
<meta charset="utf-8">
<title>VELORA – Avenue for Business Growth</title>
<link href="https://fonts.googleapis.com/css2?family=Open+Sans:wght@400;600;700;800&display=swap" rel="stylesheet">
<style>
:root{
  --blue:#5b8ec6;
  --blue-bright:#5aa7ef;
  --ink:#111111;
  --text:#333333;
  --muted:#777777;
  --light:#ebebeb;
  --nav:#0b0b0b;
  --bar:#3a3a3a;
  --white:#ffffff;
  --grey-icon:#6a6767;
}
*{box-sizing:border-box;margin:0;padding:0}
html,body{width:1200px;height:2826px;overflow:hidden}
body{font-family:"Open Sans",Arial,sans-serif;color:var(--text);background:var(--white);position:relative}
.section{position:absolute;left:0;width:1200px}

/* Header */
.site-header{top:0;height:90px;background:var(--white)}
.brand{position:absolute;left:60px;top:20px;display:flex;align-items:center;gap:14px}
.brand-dot{width:50px;height:50px;border-radius:50%;background:var(--blue)}
.brand-name{font-size:34px;font-weight:600;color:var(--blue);letter-spacing:2px}
.search{position:absolute;left:908px;top:32px;width:237px;height:55px;border:1px solid #cfcfcf;display:flex;align-items:center;padding:0 12px;font-size:17px;color:#9a9a9a}
.search svg{position:absolute;right:12px;top:15px}

/* Navigation */
.main-nav{top:90px;height:59px;background:var(--nav)}
.main-nav ul{list-style:none;position:absolute;left:60px;top:0;display:flex;height:59px}
.main-nav li{font-size:14px;color:var(--white);line-height:59px;margin-right:68px;position:relative}
.main-nav li.active{color:var(--blue-bright)}
.main-nav li.active::before{content:"";position:absolute;left:-14px;right:-14px;top:0;height:4px;background:var(--blue)}
.sign-in{position:absolute;left:1023px;top:14px;width:102px;height:32px;background:var(--blue);color:var(--white);font-size:12px;text-align:center;line-height:32px}

/* Hero */
.hero{top:149px;height:605px;background:linear-gradient(120deg,#595959 0%,#3f3f3f 45%,#6a6a6a 75%,#4a4a4a 100%)}
.hero-title{position:absolute;left:94px;top:80px;font-size:46px;font-weight:800;line-height:46px;letter-spacing:3px;color:var(--white)}
.hero-dots{position:absolute;left:565px;top:569px;display:flex;gap:16px}
.hero-dots span{width:13px;height:13px;border-radius:50%;background:#5d7fa6}
.hero-dots span.on{background:var(--blue-bright);box-shadow:0 0 0 2px #cde0f5}

/* Welcome */
.welcome{top:754px;height:201px;background:var(--light);text-align:center}
.welcome h1{margin-top:24px;font-size:30px;font-weight:400;color:var(--ink)}
.welcome .lead{margin-top:6px;font-size:17px;color:var(--blue)}
.welcome p.body{width:780px;margin:8px auto 0;font-size:13px;line-height:21px;color:var(--muted)}

/* Video */
.video-bar{top:955px;height:62px;background:var(--bar)}
.video-bar .caption{position:absolute;left:60px;top:20px;font-size:15px;color:var(--white)}
.video-bar .tools{position:absolute;right:30px;top:16px;display:flex;gap:20px}
.video-frame{top:1017px;height:345px;background:linear-gradient(180deg,#8a8565 0%,#6d6a55 45%,#4a4a44 100%)}
.play{position:absolute;left:563px;top:130px}
.video-controls{top:1362px;height:45px;background:#151515}
.video-controls svg{position:absolute;left:0;top:0}
.time{position:absolute;left:728px;top:11px;font-size:16px;color:var(--white);letter-spacing:1px}

.watch{top:1407px;height:125px;background:var(--white)}
.watch-btn{position:absolute;left:526px;top:29px;width:186px;height:50px;background:linear-gradient(180deg,#66b3f5,#4a98e6);border:1px solid #3e8ad8;color:var(--ink);font-size:12px;text-align:center;line-height:48px}

/* Experts */
.experts{top:1532px;height:442px;background:var(--light)}
.section-title{text-align:center;font-size:30px;font-weight:400;color:var(--ink)}
.experts .section-title{padding-top:31px}
.expert{position:absolute;top:99px;width:342px;height:292px}
.expert .photo{position:absolute;inset:0}
.expert .label{position:absolute;left:0;right:0;bottom:0;height:66px;background:rgba(20,20,20,.72);color:var(--white);padding:10px 0 0 32px}
.expert .name{font-size:16px}
.expert .role{font-size:12px;margin-top:2px}
.expert .top-label{position:absolute;left:32px;top:26px;color:var(--white)}
.view-profile{position:absolute;left:66px;top:150px;width:212px;height:66px;border:2px solid var(--white);color:var(--white);text-align:center;line-height:62px;font-size:16px}

/* Services */
.services{top:1974px;height:524px;background:var(--white)}
.services .section-title{padding-top:38px}
.service{position:absolute;top:96px;width:230px;text-align:center}
.service .icon{width:180px;height:180px;border-radius:50%;background:var(--blue);margin:0 auto;display:flex;align-items:center;justify-content:center}
.service .icon.grey{background:var(--grey-icon)}
.service h3{margin-top:18px;font-size:16px;font-weight:400;color:var(--ink)}
.service .rule{width:196px;height:2px;background:#bdbdbd;margin:11px auto 0}
.service p{margin-top:14px;font-size:13px;line-height:20px;color:var(--muted)}
.learn{display:block;width:137px;height:40px;margin:22px auto 0;background:var(--ink);color:var(--white);font-size:11px;line-height:40px}

/* Footer */
.site-footer{top:2498px;height:249px;background:var(--light)}
.footer-col{position:absolute;top:40px}
.footer-col h4{font-size:22px;font-weight:400;color:var(--blue)}
.footer-links{list-style:none}
.footer-links li{font-size:22px;color:var(--blue);line-height:46px}
.footer-col .small{margin-top:10px;font-size:12px;line-height:18px;color:var(--muted);text-transform:uppercase}
.footer-col .phones{margin-top:20px;font-size:12px;line-height:18px;color:var(--muted)}
.socials{display:flex;gap:10px;margin-top:22px}
.socials span{width:60px;height:60px;display:block}
.socials .s1{background:#2f5e9e}.socials .s2{background:var(--blue-bright)}.socials .s3{background:#d9483b}
.email{margin-top:22px;width:235px;height:48px;border:1px solid #bdbdbd;background:var(--white);font-size:17px;color:#8a8a8a;line-height:46px;padding-left:10px}
.signup{margin-top:18px;width:88px;height:32px;background:var(--ink);color:var(--white);font-size:11px;text-align:center;line-height:32px}

.copyright{top:2747px;height:79px;background:var(--ink);color:var(--white);text-align:center;font-size:16px;line-height:79px}
</style>
</head>
<body>

<header class="section site-header">
  <div class="brand"><span class="brand-dot"></span><span class="brand-name">VELORA</span></div>
  <div class="search">search
    <svg width="24" height="24" viewBox="0 0 24 24"><circle cx="10" cy="10" r="7" fill="none" stroke="#5b8ec6" stroke-width="3"/><line x1="15" y1="15" x2="22" y2="22" stroke="#5b8ec6" stroke-width="3"/></svg>
  </div>
</header>

<nav class="section main-nav">
  <ul>
    <li class="active">HOME</li><li>ABOUT US</li><li>SERVICES</li><li>SOLUTIONS</li><li>CONTACTS</li>
  </ul>
  <div class="sign-in">SIGN IN</div>
</nav>

<section class="section hero" role="img" aria-label="Excited businessman in front of a rising wooden growth arrow on a grey wall">
  <h2 class="hero-title">AVENUE FOR<br>BUSINESS<br>GROWTH</h2>
  <div class="hero-dots"><span></span><span></span><span class="on"></span></div>
</section>

<section class="section welcome">
  <h1>WELCOME TO OUR AVENUE !!!</h1>
  <p class="lead">Phasellus porta. Fusce suscipit varius mi. Cum sociis natoque penatibus et magnis dis</p>
  <p class="body">Phasellus porta. Fusce suscipit varius mi. Cum sociis natoque penatibus et magnis dis parturient montes, nascetur ridiculus orbi nunc odio, gravida at, cursus nec, luctus a, lorem.Phasellus porta. Fusce suscipit varius mi. Cum sociis natoque penatibus et magnis disPhasellus porta. Fusce suscipit varius mi. Cum sociis natoque dis parturient montes.lorem.</p>
</section>

<div class="section video-bar">
  <span class="caption">Opportunities with incredible money making potential.........................................</span>
  <div class="tools">
    <svg width="36" height="28" viewBox="0 0 36 28"><path d="M18 26 L4 13 A7.5 7.5 0 0 1 18 5 A7.5 7.5 0 0 1 32 13 Z" fill="#fff"/></svg>
    <svg width="36" height="28" viewBox="0 0 36 28"><g fill="none" stroke="#fff" stroke-width="3"><rect x="3" y="12" width="16" height="9" rx="4.5" transform="rotate(-35 11 16)"/><rect x="16" y="6" width="16" height="9" rx="4.5" transform="rotate(-35 24 10)"/></g></svg>
  </div>
</div>

<section class="section video-frame" role="img" aria-label="Video still: businessman walking along a road with the word success painted on it">
  <svg class="play" width="74" height="74" viewBox="0 0 74 74"><circle cx="37" cy="37" r="33" fill="rgba(255,255,255,.25)" stroke="#fff" stroke-width="5"/><path d="M29 22 L53 37 L29 52 Z" fill="#fff"/></svg>
</section>

<div class="section video-controls">
  <svg width="1200" height="45" viewBox="0 0 1200 45">
    <path d="M22 15 L42 22 L22 29 Z" fill="#fff"/>
    <line x1="78" y1="6" x2="78" y2="39" stroke="#333" stroke-width="2"/>
    <rect x="101" y="17" width="610" height="11" rx="5.5" fill="#2a2a2a"/>
    <rect x="101" y="17" width="240" height="11" rx="5.5" fill="#3d7fd6"/>
    <rect x="336" y="15" width="46" height="15" rx="6" fill="#d8d8d8"/>
    <line x1="868" y1="6" x2="868" y2="39" stroke="#333" stroke-width="2"/>
    <path d="M892 18 h6 l7 -6 v21 l-7 -6 h-6 Z" fill="#fff"/>
    <path d="M910 17 q4 5 0 10 M914 14 q7 8 0 16" stroke="#fff" stroke-width="2" fill="none"/>
    <rect x="948" y="19" width="150" height="7" rx="3.5" fill="#2a2a2a"/>
    <rect x="1072" y="17" width="22" height="11" rx="5" fill="#e0e0e0"/>
    <line x1="1125" y1="6" x2="1125" y2="39" stroke="#333" stroke-width="2"/>
    <rect x="1155" y="15" width="22" height="15" fill="none" stroke="#fff" stroke-width="2.5"/>
  </svg>
  <span class="time">4.25 / 7.12</span>
</div>

<section class="section watch"><div class="watch-btn">WATCH THE VIDEO</div></section>

<section class="section experts">
  <h2 class="section-title">INTRODUCING OUR BUSINESS EXPERTS</h2>
  <article class="expert" style="left:60px">
    <div class="photo" role="img" aria-label="Portrait of a man in a dark suit" style="background:linear-gradient(135deg,#8c8c8c,#5a5a5a 60%,#2c2c2c)"></div>
    <div class="label"><div class="name">OWEN CALDER</div><div class="role">President • Clearwater Ideas</div></div>
  </article>
  <article class="expert" style="left:430px">
    <div class="photo" role="img" aria-label="Portrait of a businessman seated in an office" style="background:linear-gradient(135deg,#3b4452,#252a33 55%,#4a4c52)"></div>
    <div class="top-label"><div class="name">MILES HARTWELL</div><div class="role">CEO • The Circuit Room</div></div>
    <div class="view-profile">VIEW PROFILE</div>
  </article>
  <article class="expert" style="left:797px">
    <div class="photo" role="img" aria-label="Portrait of a smiling man with glasses" style="background:linear-gradient(135deg,#b7c6cc,#8d9aa0 55%,#56605f)"></div>
    <div class="label"><div class="name">ELIAS NORCOTT</div><div class="role">Senior Partner • LayerMint</div></div>
  </article>
</section>

<section class="section services">
  <h2 class="section-title">OUR SERVICES</h2>
  <div class="service" style="left:77px">
    <div class="icon"><svg width="100" height="100" viewBox="0 0 100 100"><path d="M82 18 C60 18 44 30 36 50 L50 64 C70 56 82 40 82 18 Z" fill="#fff"/><path d="M36 50 L22 52 L14 62 L30 62 Z M50 64 L48 78 L38 86 L38 70 Z" fill="#fff"/><path d="M30 70 L18 82" stroke="#fff" stroke-width="6"/><circle cx="62" cy="38" r="6" fill="#5b8ec6"/></svg></div>
    <h3>CONSECTETUER</h3><div class="rule"></div>
    <p>Lorem ipsum dolor sit amet, con-sectetuer adipiscing elit. Praesent vestibulum moles lacus. Aenean nonummy hendrerit.</p>
    <span class="learn">LEARN MORE</span>
  </div>
  <div class="service" style="left:350px">
    <div class="icon"><svg width="100" height="100" viewBox="0 0 100 100"><circle cx="60" cy="34" r="15" fill="#fff"/><path d="M36 80 C36 58 84 58 84 80 Z" fill="#fff"/><circle cx="40" cy="40" r="14" fill="#fff" stroke="#5b8ec6" stroke-width="4"/><path d="M14 84 C14 62 66 62 66 84 Z" fill="#fff" stroke="#5b8ec6" stroke-width="4"/></svg></div>
    <h3>ADIPISCING ELIT</h3><div class="rule"></div>
    <p>Lorem ipsum dolor sit amet, con-sectetuer adipiscing elit. Praesent vestibulum moles lacus. Aenean nonummy hendrerit.</p>
    <span class="learn">LEARN MORE</span>
  </div>
  <div class="service" style="left:622px">
    <div class="icon"><svg width="100" height="100" viewBox="0 0 100 100"><path d="M38 30 v-8 h24 v8" fill="none" stroke="#fff" stroke-width="6"/><rect x="14" y="30" width="72" height="50" rx="6" fill="#fff"/><rect x="14" y="50" width="72" height="4" fill="#5b8ec6"/><rect x="44" y="46" width="12" height="12" fill="#fff" stroke="#5b8ec6" stroke-width="3"/></svg></div>
    <h3>PENATIBUS ET</h3><div class="rule"></div>
    <p>Lorem ipsum dolor sit amet, con-sectetuer adipiscing elit. Praesent vestibulum moles lacus. Aenean nonummy hendrerit.</p>
    <span class="learn">LEARN MORE</span>
  </div>
  <div class="service" style="left:895px">
    <div class="icon grey"><svg width="100" height="100" viewBox="0 0 100 100"><rect x="16" y="46" width="14" height="36" fill="#fff"/><path d="M36 46 L50 20 C56 16 62 20 60 28 L56 42 H80 C86 42 88 48 86 52 L80 78 C78 82 76 84 70 84 H36 Z" fill="#fff"/></svg></div>
    <h3>NONUMMY HEND</h3><div class="rule"></div>
    <p>Lorem ipsum dolor sit amet, con-sectetuer adipiscing elit. Praesent vestibulum moles lacus. Aenean nonummy hendrerit.</p>
    <span class="learn">LEARN MORE</span>
  </div>
</section>

<footer class="section site-footer">
  <div class="footer-col" style="left:105px;top:28px">
    <ul class="footer-links"><li>ABOUT US</li><li>OUR TEAM</li><li>LEGAL</li><li>CONTACT US</li></ul>
  </div>
  <div class="footer-col" style="left:354px">
    <h4>CONTACT US</h4>
    <p class="small">Lorem ipsum dolor sit amet,<br>consectetuer adipiscing elit.<br>Praesent vestibulum molestie</p>
    <p class="phones">+1800 555 010 0412<br>+1800 555 010 0413</p>
  </div>
  <div class="footer-col" style="left:607px">
    <h4>FOLLOW US</h4>
    <div class="socials"><span class="s1"></span><span class="s2"></span><span class="s3"></span></div>
  </div>
  <div class="footer-col" style="left:887px">
    <h4>TO KNOW MORE</h4>
    <div class="email">email address</div>
    <div class="signup">SIGN UP</div>
  </div>
</footer>

<div class="section copyright">VELORA @ 2014. All Copyrights reserved.</div>

</body>
</html>
```